Pemberlux: Smart Quotes for Wine Lovers

Hello. I am completing book of quotes for wine lovers. Need the text formatted so that it is easy to read and aesthetically pleasing...modern, clean, smart. Number the pages. The cover is complete. Book is small square. 7.5 by 7.5 inches. If you want to show me first few pages that would be awesome. Thank you!
Updates

I edited the quotes so if you downloaded first ones, please grab these ones instead, thank you! 

Target Market(s)

wine lovers. Urban. Modern.

Industry/Entity Type

Quotes

Requirements
Should not have
• No color. black and white only.

```html
<!DOCTYPE html>
<html lang="en">
<head>
<meta charset="utf-8">
<title>Pemberlux: Smart Quotes for Wine Lovers</title>
<link href="https://fonts.googleapis.com/css2?family=PT+Sans:wght@400;700&display=swap" rel="stylesheet">
<style>
  :root {
    --paper: #000000;
    --ink: #ffffff;
    --gutter: #5a5a5a;
    --art-light: #2e2e2e;
    --art-dark: #161616;
  }
  * { margin: 0; padding: 0; box-sizing: border-box; }
  html, body {
    width: 1200px;
    height: 600px;
    overflow: hidden;
    background: var(--paper);
  }
  .spread {
    position: relative;
    width: 1200px;
    height: 600px;
    display: flex;
    background: var(--paper);
    color: var(--ink);
    font-family: "PT Sans", "Verdana", sans-serif;
  }
  .page {
    position: relative;
    width: 600px;
    height: 600px;
    text-align: center;
  }
  .page--left { border-right: 1px solid var(--gutter); }
  .page-number {
    position: absolute;
    top: 60px;
    font-size: 13px;
    letter-spacing: 0.5px;
  }
  .page--left .page-number { left: 62px; }
  .page--right .page-number { right: 62px; }
  .quote {
    position: absolute;
    top: 133px;
    left: 0;
    right: 0;
    font-size: 44px;
    line-height: 50px;
    font-weight: 400;
    letter-spacing: 1.2px;
  }
  .attribution {
    margin-top: 12px;
    font-size: 13px;
    line-height: 16px;
    letter-spacing: 1px;
    text-transform: uppercase;
  }
  .glasses-art {
    position: absolute;
    top: 353px;
    left: 50%;
    width: 50px;
    height: 121px;
    transform: translateX(-50%);
    border-radius: 6px;
    background: linear-gradient(180deg, var(--art-light), var(--art-dark));
  }
  .biography {
    position: absolute;
    top: 502px;
    left: 0;
    right: 0;
    font-size: 8px;
    line-height: 10px;
    font-weight: 700;
  }
</style>
</head>
<body>
<main class="spread">
  <section class="page page--left">
    <span class="page-number">42</span>
    <blockquote class="quote">
      <p>The connoisseur does<br>not drink wine but<br>tastes its secrets</p>
      <p class="attribution">–Aurelio Vantresca</p>
    </blockquote>
    <div class="glasses-art" role="img" aria-label="Line illustration of two overlapping wine glasses"></div>
    <p class="biography">Aurelio Benedetto Vantresca i Moreval (1904–1989)<br>1st Marqués de Vantresca de Ostral. Spanish Surrealist Painter.</p>
  </section>
  <section class="page page--right">
    <span class="page-number">43</span>
    <blockquote class="quote">
      <p>Wine is the divine<br>juice of September</p>
      <p class="attribution">–Montclair</p>
    </blockquote>
    <div class="glasses-art" role="img" aria-label="Line illustration of two overlapping wine glasses"></div>
    <p class="biography">Étienne-Louis Marchaud (1694 –1778). Known by his “nom de plume” Montclair.<br>French Enlightenment Writer, Historian and Philosopher.</p>
  </section>
</main>
</body>
</html>
```